hotel's Website

Hotels website redesign for reference pictures, logo etc see http://restwellharbour.co.uk/

1. 2-3 Special offers on the main page.
2. Booking calender
3. Location Map
4. Picture gallery.
5. Journeymarks reviews.
6. short description
7. Social Media sharing.
8 Phone number and address.

Industry/Entity Type

Hotel

Requirements
Must have
• 1. 2-3 Special offers on the main page.
2. Booking calender
3. Location Map
4. Picture gallery.
5. Journeymarks reviews.
6. short description
7. Social Media sharing.

```html
<!DOCTYPE html>
<html lang="en">
<head>
<meta charset="utf-8">
<title>Restwell Harbour – Hotel</title>
<link href="https://fonts.googleapis.com/css2?family=Roboto+Slab:wght@300;400;700&family=Roboto:wght@400;500;700&family=Roboto+Condensed:wght@400;700&display=swap" rel="stylesheet">
<style>
:root{
  --night:#0d3f86;
  --brand-blue:#0c58b8;
  --yellow:#ffe512;
  --ink:#333;
  --text:#666;
  --red:#e01b2a;
  --link:#1a56b0;
  --rule:#ddd;
  --white:#fff;
}
*{box-sizing:border-box;margin:0;padding:0}
html,body{width:1059px;height:1200px;overflow:hidden}
body{position:relative;font-family:"Roboto Slab",serif;color:var(--ink);background:var(--night)}
.abs{position:absolute}
.backdrop{position:absolute;inset:0;background:linear-gradient(180deg,#1f5fb0 0%,#0f4a98 30%,#123e7a 48%,#0b3a7d 60%,#0a3a80 100%)}
.translate{top:8px;left:781px;font:700 10px "Roboto",sans-serif;color:#fff;display:flex;align-items:center;gap:5px}
.translate .select{width:98px;height:22px;background:#fff;border:1px solid #bbb;color:#333;font-weight:400;display:flex;align-items:center;padding:0 6px;gap:6px}
.translate .flag{width:18px;height:12px;background:#23408e}
.phone-top{top:34px;left:794px;font:500 14px "Roboto",sans-serif;color:#fff;display:flex;align-items:center;gap:6px}
.mail-top{top:55px;left:748px;font:500 10.5px "Roboto",sans-serif;color:#fff;display:flex;align-items:center;gap:6px}
.sheet{left:117px;top:72px;width:827px;height:1128px;background:var(--white);border-radius:8px 8px 0 0}
.nav{left:132px;top:93px;width:794px;height:42px;background:var(--brand-blue);border-radius:4px 4px 0 0;display:flex;align-items:center;font:400 10.5px "Roboto Slab",serif;letter-spacing:.5px;color:#fff}
.nav .home{width:47px;height:42px;background:var(--yellow);display:flex;align-items:center;justify-content:center;border-radius:4px 0 0 0}
.nav .item{position:absolute;top:15px}
.logo{left:480px;top:41px;width:103px;height:113px;background:#fff;text-align:center;font-family:"Roboto Slab",serif;z-index:5;display:flex;flex-direction:column;align-items:center;justify-content:space-between;padding:5px 0 4px}
.logo .loc{font-size:7px;color:var(--brand-blue);line-height:1}
.logo .name{font:700 15px/1.15 "Roboto Slab",serif;color:var(--brand-blue)}
.logo .by{font-size:6.5px;color:#333;line-height:1}
.slider{left:132px;top:136px;width:794px;height:362px;background:linear-gradient(135deg,#8a7d6a 0%,#c9b79a 35%,#e7c93a 55%,#d8c9b5 75%,#b08a4a 100%);border-radius:0 0 8px 8px;overflow:hidden}
.thumb-strip{left:0;top:288px;width:794px;height:74px;background:rgba(0,0,0,.35)}
.thumb{position:absolute;top:9px;width:94px;height:56px;border:2px solid var(--yellow);border-radius:4px}
.thumb.on{top:-1px;width:124px;height:70px}
.arrow{position:absolute;top:146px}
h2.section{position:absolute;font:400 15.5px "Roboto Slab",serif;color:#333;display:flex;align-items:center;gap:8px;border-bottom:1px solid var(--rule);width:474px;padding-bottom:4px}
.bullet{width:16px;height:16px;border-radius:50%;background:linear-gradient(180deg,#f7a81b 0%,#e8432b 60%,#f7c61b 100%)}
.intro{left:162px;top:569px;width:472px;font:300 10.6px/15px "Roboto Slab",serif;color:var(--text);letter-spacing:.35px}
.more{font:400 9.5px "Roboto Slab",serif;color:#222;display:flex;align-items:center;gap:5px}
.more i{width:14px;height:14px;border-radius:50%;background:#111;display:inline-block;position:relative}
.more i::after{content:"";position:absolute;left:4px;top:4px;width:4px;height:4px;border-right:1.5px solid var(--yellow);border-top:1.5px solid var(--yellow);transform:rotate(45deg)}
.offers{left:164px;top:738px;width:463px;height:192px;border:1px solid #e3e3e3;background:linear-gradient(180deg,#f3f3f3,#fff)}
.offer{position:absolute;top:12px;width:182px;height:164px;border:6px solid var(--yellow)}
.offer .cap{position:absolute;right:6px;bottom:6px;width:86px;padding:4px;background:rgba(255,255,255,.75);text-align:center;font:700 13px/1.1 "Roboto Condensed",sans-serif;color:#222}
.offer .cap b{color:var(--red);font-size:20px;display:block}
.offer .cap em{font-style:normal;color:var(--brand-blue);font-size:22px;display:block}
.nudge{position:absolute;top:96px;width:22px;height:40px;background:#222;display:flex;align-items:center;justify-content:center}
.nudge.l{left:-5px;border-radius:20px 0 0 20px}
.nudge.r{right:-5px;border-radius:0 20px 20px 0}
.newsletter{left:160px;top:946px;width:475px;height:28px;display:flex;font:400 10.5px "Roboto Slab",serif}
.newsletter .label{width:101px;background:#2b2b2b;color:#fff;font-weight:700;display:flex;align-items:center;justify-content:center;letter-spacing:.5px}
.newsletter .field{width:305px;border:1px solid #ccc;background:linear-gradient(180deg,#fff,#eee);color:#999;display:flex;align-items:center;padding-left:17px}
.newsletter .btn{margin-left:5px;width:64px;background:#9a9a9a;color:#fff;display:flex;align-items:center;justify-content:center;border:1px solid #888}
.panel-head{position:absolute;left:673px;width:231px;height:29px;background:var(--yellow);font:700 12px "Roboto Slab",serif;color:#6b5a1a;display:flex;align-items:center;padding-left:18px;letter-spacing:.4px}
.panel-head::before,.panel-head::after{content:"";position:absolute;top:29px;border-top:8px solid #555;border-left:8px solid transparent}
.panel-head::before{left:0;border-left:0;border-right:8px solid transparent}
.panel-head::after{right:0}
.card{position:absolute;left:682px;width:213px;background:#fff;border-radius:0 0 8px 8px;box-shadow:0 3px 5px rgba(0,0,0,.15)}
.month{position:absolute;left:8px;top:10px;font:400 16px "Roboto Condensed",sans-serif;color:#444}
.next{position:absolute;right:8px;top:11px;width:14px;height:14px;border-radius:50%;background:#eee;border:1px solid #ccc}
.cal{position:absolute;left:5px;top:33px;width:203px;border-collapse:collapse;font:400 9.5px "Roboto",sans-serif;color:#444;text-align:center}
.cal th{background:#9b9b9b;color:#fff;font:700 8.5px "Roboto",sans-serif;height:21px}
.cal td{border:1px solid #ccc;height:21.7px}
.cal td.today{color:var(--red);font-weight:700}
.cal td.blank{border:none;border-top:1px solid #ccc}
.book-btn{position:absolute;right:12px;top:167px;padding:4px 6px;background:var(--yellow);border:1px solid #d1bb00;border-radius:3px;font:400 9px "Roboto Slab",serif;color:#222}
.review{position:absolute;left:42px;top:14px;width:162px;font:300 10px/15px "Roboto Slab",serif;color:#555;letter-spacing:.3px}
.quote{position:absolute;font:700 40px Georgia,serif;color:#ccc;line-height:1}
.follow{left:690px;top:955px;font:400 13.5px "Roboto Slab",serif;color:#444}
.social{position:absolute;top:947px;width:26px;height:26px;border-radius:5px}
.divider{left:160px;top:1004px;width:740px;height:1px;background:#e5e5e5}
.foot-h{position:absolute;top:1024px;font:700 14.5px "Roboto Condensed",sans-serif;color:var(--red)}
.qlink{position:absolute;font:400 10.5px "Roboto",sans-serif;color:#444;display:flex;align-items:center;gap:7px}
.qlink i{width:10px;height:8px;background:var(--yellow);clip-path:polygon(0 25%,55% 25%,55% 0,100% 50%,55% 100%,55% 75%,0 75%)}
.vsep{position:absolute;top:1026px;width:1px;height:125px;background:#ddd}
.partner-note{left:396px;top:1053px;width:170px;font:400 8px/10px "Roboto",sans-serif;color:#555}
.partners{left:396px;top:1088px;font:400 8.6px/10px "Roboto Slab",serif;color:var(--link);list-style:none}
.map{left:594px;top:1056px;width:120px;height:96px;background:linear-gradient(135deg,#dfe6c9,#cfd9b4 50%,#e9e4d3)}
.contact{position:absolute;left:735px;font:400 10.5px/14px "Roboto",sans-serif;color:#444;display:flex;gap:12px;width:180px}
.contact svg{flex:none;margin-top:1px}
.footer{left:117px;top:1166px;width:827px;height:34px;background:var(--yellow);font:400 10.5px "Roboto",sans-serif;color:#333;display:flex;align-items:center;justify-content:center}
</style>
</head>
<body>
<div class="backdrop" role="img" aria-label="Night view of a river city skyline with an illuminated bridge under a deep blue sky"></div>

<div class="abs translate">Translate to : <span class="select"><span class="flag"></span>English <svg width="8" height="5" style="margin-left:auto"><path d="M0 0h8L4 5z" fill="#333"/></svg></span></div>
<div class="abs phone-top"><svg width="18" height="18" viewBox="0 0 18 18"><circle cx="9" cy="9" r="8" fill="none" stroke="#fff" stroke-width="1.5"/><path d="M6 5l2 2-1 1c.5 1.2 1.6 2.3 2.8 2.8l1-1 2 2-1.2 1.2C8.5 13 5 9.5 4.8 6.2z" fill="#fff"/></svg>+ 44 (0) 20 7946 0123</div>
<div class="abs mail-top"><svg width="16" height="11" viewBox="0 0 16 11"><rect x=".5" y=".5" width="15" height="10" fill="none" stroke="#fff"/><path d="M.5.5l7.5 6 7.5-6" fill="none" stroke="#fff"/></svg>STAY@RESTWELLHARBOUR.CO.UK</div>

<div class="abs sheet"></div>

<nav class="abs nav">
  <div class="home"><svg width="18" height="15" viewBox="0 0 18 15"><path d="M9 0l9 7h-2.5v8h-4.5v-5h-4v5h-4.5v-8h-2.5z" fill="#333"/></svg></div>
  <span class="item" style="left:63px">OUR ROOMS</span>
  <span class="item" style="left:149px">ATTRACTIONS</span>
  <span class="item" style="left:244px">LONDON EVENTS</span>
  <span class="item" style="left:468px">SPECIAL OFFERS</span>
  <span class="item" style="left:574px">PHOTOS</span>
  <span class="item" style="left:642px">DIRECTIONS</span>
  <span class="item" style="left:729px">CONTACT</span>
</nav>

<div class="abs logo">
  <div class="loc">LONDON - VICTORIA</div>
  <div class="name">Restwell<br>Harbour</div>
  <div class="by">BY HARBOURLINE HOTELS</div>
</div>

<section class="abs slider" role="img" aria-label="Photo gallery: bright hotel lounge with yellow armchairs, colourful cushions and a spotted rug">
  <svg class="arrow" style="left:28px" width="16" height="24"><path d="M13 2L3 12l10 10" fill="none" stroke="#ffd400" stroke-width="4"/></svg>
  <svg class="arrow" style="right:28px" width="16" height="24"><path d="M3 2l10 10L3 22" fill="none" stroke="#ffd400" stroke-width="4"/></svg>
  <div class="abs thumb-strip">
    <div class="thumb" style="left:28px;background:linear-gradient(135deg,#eee,#c0302b)" role="img" aria-label="Double bedroom"></div>
    <div class="thumb" style="left:130px;background:linear-gradient(135deg,#5a4a3a,#c8b9a4)" role="img" aria-label="Breakfast counter"></div>
    <div class="thumb" style="left:233px;background:linear-gradient(135deg,#d8c7ab,#8a6a4a)" role="img" aria-label="Kitchenette"></div>
    <div class="thumb on" style="left:335px;background:linear-gradient(135deg,#c9b79a,#e7c93a,#d46a3a)" role="img" aria-label="Lounge"></div>
    <div class="thumb" style="left:468px;background:linear-gradient(135deg,#c88a4a,#7a4a2a)" role="img" aria-label="Dining room"></div>
    <div class="thumb" style="left:571px;background:linear-gradient(135deg,#f4f4f4,#cfd5da)" role="img" aria-label="Bathroom"></div>
    <div class="thumb" style="left:674px;background:linear-gradient(135deg,#e8dcc4,#b8343a)" role="img" aria-label="Twin bedroom"></div>
  </div>
</section>

<h2 class="section" style="left:160px;top:536px"><span class="bullet"></span>Welcome To Restwell Harbour</h2>
<p class="abs intro">Lorem ipsum dolor sit amet, consectetuer adipiscing elit, sed diam nonummy nibh euismod tincidunt ut laoreet dolore magna aliquam erat volutpat. Ut wisi enim ad minim veniam, quis nostrud exerci tation ullamcorper suscipit lobortis nisl ut aliquip. Lorem ipsum dolor sit amet, consectetuer adipiscing elit, sed diam nonummy nibh euismod tincidunt ut laoreet dolore magna aliquam erat volutpat. Ut wisi enim ad minim veniam, quis nostrud exerci tation ullamcorper suscipit lobortis nisl ut aliquip.</p>
<a class="abs more" style="left:568px;top:658px"><i></i>Read more</a>

<h2 class="section" style="left:160px;top:702px"><span class="bullet"></span>Our Special Offers</h2>
<section class="abs offers">
  <div class="nudge l"><svg width="8" height="12"><path d="M7 1L2 6l5 5" fill="none" stroke="#ffd400" stroke-width="2"/></svg></div>
  <div class="offer" style="left:30px;background:linear-gradient(135deg,#5a4032,#c89a7a 50%,#e8d6c6)" role="img" aria-label="Spa foot treatment in a stone bowl">
    <div class="cap"><b>SPA</b>TREATMENT<br>Save <span style="color:var(--red);font-size:20px">25%</span></div>
  </div>
  <div class="offer" style="left:253px;background:linear-gradient(135deg,#e6e0da,#b56a7a 50%,#5a5058)" role="img" aria-label="Shopper browsing handbags in a boutique">
    <div class="cap"><b>Shopping</b>IN<em>LONDON</em></div>
  </div>
  <div class="nudge r"><svg width="8" height="12"><path d="M1 1l5 5-5 5" fill="none" stroke="#fff" stroke-width="2"/></svg></div>
</section>

<form class="abs newsletter"><span class="label">NEWSLETTER</span><span class="field">E-mail address</span><span class="btn">Subscribe</span></form>

<div class="panel-head" style="top:532px">BOOKING CALENDAR</div>
<section class="card" style="top:563px;height:192px">
  <div class="month">November 2013</div><div class="next"></div>
  <table class="cal">
    <tr><th>MON</th><th>TUE</th><th>WED</th><th>THU</th><th>FRI</th><th>SAT</th><th>SUN</th></tr>
    <tr><td>1</td><td>2</td><td>3</td><td>4</td><td>5</td><td>6</td><td>7</td></tr>
    <tr><td>8</td><td>9</td><td>10</td><td>11</td><td>12</td><td>13</td><td>14</td></tr>
    <tr><td>15</td><td>16</td><td>17</td><td>18</td><td>19</td><td>20</td><td class="today">21</td></tr>
    <tr><td>22</td><td>23</td><td>24</td><td>25</td><td>26</td><td>27</td><td>28</td></tr>
    <tr><td>29</td><td>30</td><td class="blank" colspan="5"></td></tr>
  </table>
  <div class="book-btn">Click To Book</div>
</section>

<div class="panel-head" style="top:776px;padding-left:24px;font-weight:400;color:#333"><span style="width:12px;height:12px;border-radius:50%;background:#333;margin-right:6px"></span>Journeymarks REVIEWS
  <svg style="margin-left:auto;margin-right:10px" width="28" height="10"><path d="M12 5H3M6 1L2 5l4 4M16 5h9M22 1l4 4-4 4" fill="none" stroke="#333" stroke-width="2"/></svg></div>
<section class="card" style="top:807px;height:121px">
  <span class="quote" style="left:14px;top:4px">“</span>
  <p class="review">Lorem ipsum dolor sit amet, adipiscing elit. Mauris felis ante,semper et, accumsan quis diam.tincidunt felis nec magna feugiat ulla atvesti bulum.</p>
  <span class="quote" style="left:82px;top:86px">”</span>
  <span class="abs" style="right:24px;top:98px;font:italic 700 9px 'Roboto',sans-serif;color:#444">Read More</span>
</section>

<div class="abs follow">Follow Us</div>
<span class="social" style="left:767px;background:#3b5a9a" aria-label="Social link"></span>
<span class="social" style="left:800px;background:#38a8dc" aria-label="Social link"></span>
<span class="social" style="left:833px;background:#1f6fa8" aria-label="Social link"></span>
<span class="social" style="left:866px;background:#f0782a" aria-label="Feed link"></span>

<div class="abs divider"></div>

<h3 class="foot-h" style="left:161px">Quick Links</h3>
<a class="qlink" style="left:161px;top:1054px"><i></i>Home</a>
<a class="qlink" style="left:161px;top:1082px"><i></i>Our Rooms</a>
<a class="qlink" style="left:161px;top:1111px"><i></i>Attractions</a>
<a class="qlink" style="left:161px;top:1140px"><i></i>London Events</a>
<a class="qlink" style="left:267px;top:1054px"><i></i>Special Offers</a>
<a class="qlink" style="left:267px;top:1082px"><i></i>Photos</a>
<a class="qlink" style="left:267px;top:1111px"><i></i>Direction</a>
<a class="qlink" style="left:267px;top:1140px"><i></i>Contact Us</a>
<span class="vsep" style="left:380px"></span>

<h3 class="foot-h" style="left:396px">Partner Hotels</h3>
<p class="abs partner-note">This hotel is owned and operated by the Meridale Hotel Group, please take a look of some of our other hotels below:</p>
<ul class="abs partners">
  <li>Lanternway Rooms - Canal Side</li>
  <li>Lanternway Express - Court Row</li>
  <li>Greyfield House Hotel</li>
  <li>Simplestay Eastbank</li>
  <li>Simplestay Westgate</li>
  <li>Restwell Suites - Kingsmere</li>
</ul>
<span class="vsep" style="left:577px"></span>

<h3 class="foot-h" style="left:594px">Contact Info</h3>
<div class="abs map" role="img" aria-label="Location map of the streets around the hotel"></div>
<div class="contact" style="top:1054px"><svg width="10" height="13" viewBox="0 0 10 13"><path d="M5 0a5 5 0 0 1 5 5c0 3-5 8-5 8S0 8 0 5a5 5 0 0 1 5-5z" fill="#1a56b0"/><circle cx="5" cy="5" r="2" fill="#fff"/></svg><span>42 Marlow Terrace, Eastbank London EB4 2QT</span></div>
<div class="contact" style="top:1092px"><svg width="12" height="12" viewBox="0 0 12 12"><path d="M2 0l3 3-1.5 1.5c.7 1.6 2.3 3.2 4 4L9 7l3 3-2 2C5 12 0 7 0 2z" fill="#1a56b0"/></svg><span>+ 44 (0) 20 7946 0123</span></div>
<div class="contact" style="top:1115px"><svg width="14" height="11" viewBox="0 0 14 11"><rect x="2" y="4" width="10" height="7" rx="1" fill="#1a56b0"/><path d="M0 4C2 0 12 0 14 4" fill="none" stroke="#1a56b0" stroke-width="2"/></svg><span>+ 44 (0) 20 7946 0588</span></div>
<div class="contact" style="top:1138px"><svg width="13" height="10" viewBox="0 0 13 10"><rect width="13" height="10" fill="#1a56b0"/><path d="M0 0l6.5 5L13 0" fill="none" stroke="#fff"/></svg><span>stay@restwellharbour.co.uk</span></div>

<footer class="abs footer">© 2013 Restwell Harbour &nbsp;|&nbsp; All Rights Reserved</footer>
</body>
</html>
```